Meridale Bed Company Needs Business Card

Looking for a very nice looking business card. Creative but not extravagant. We sell beds and pillows across the U.S. and need something professional but catchy. I have attached the logo.

Name : Devin Holt
Title : President
Phone : (800) 471-2960
Email: sleep@quilmora.com
Website: www.quilmora.com

Can be single-sided or double-sided
horizontal or vertical

Can use Blues/Greys

Target Market(s)

Mass Market

Industry/Entity Type

Retail

Contact Information for Business Card

Name : Devin Holt
Title : President
Phone : (800) 471-2960
Email: sleep@quilmora.com
Website: www.quilmora.com

Requirements
Must have
• Clean, Modern, Smooth
• Can use Blues/Greys
• On the other side without the information - have something simple like www.quilmora.com or our logo
Nice to have
• Surprise me
Should not have
• Nothing crazy, nothing cluttered

```html
<!DOCTYPE html>
<html lang="en">
<head>
<meta charset="utf-8">
<title>Quilmora Business Card</title>
<link rel="stylesheet" href="https://fonts.googleapis.com/css2?family=Questrial&display=swap">
<style>
  :root {
    --page-bg: #e8e6e3;
    --card-white: #ffffff;
    --card-mist: #eeeff1;
    --frame-grey: #e2e3e6;
    --frame-blue: #d5ebf4;
    --brand-blue: #34b5de;
    --brand-blue-deep: #1c88b2;
    --name-blue: #3fb1da;
    --ink: #3c3d40;
    --ink-soft: #7a7b7e;
    --slate: #4b4c4f;
    --slate-dark: #3a3b3d;
    --text-font: "Questrial", "Helvetica Neue", Arial, sans-serif;
  }
  * { margin: 0; padding: 0; box-sizing: border-box; }
  html, body {
    width: 1200px;
    height: 1023px;
    overflow: hidden;
    background: var(--page-bg);
  }
  .card-layout {
    width: 1200px;
    height: 1023px;
    display: flex;
    align-items: center;
    justify-content: center;
    gap: 60px;
  }
  .business-card {
    width: 500px;
    height: 286px;
    display: block;
    filter: drop-shadow(0 6px 14px rgba(0, 0, 0, 0.18));
    font-family: var(--text-font);
  }
  .wordmark { font-family: var(--text-font); fill: var(--brand-blue); font-weight: 400; }
  .holder-name { fill: var(--name-blue); font-size: 13px; }
  .holder-title { fill: var(--ink-soft); font-size: 8.5px; }
  .contact-line { fill: var(--ink); font-size: 8px; }
  .contact-icon { fill: none; stroke: var(--brand-blue); stroke-width: 0.9; }
</style>
</head>
<body>
<main class="card-layout">

  <!-- Front: contact side -->
  <svg class="business-card card-front" viewBox="0 0 350 200" aria-label="Business card front">
    <defs>
      <linearGradient id="frontFill" x1="0" y1="0" x2="0" y2="1">
        <stop offset="0" stop-color="var(--card-white)"/>
        <stop offset="1" stop-color="var(--card-mist)"/>
      </linearGradient>
      <clipPath id="frontClip"><rect width="350" height="200" rx="10"/></clipPath>
    </defs>
    <rect width="350" height="200" rx="10" fill="url(#frontFill)"/>
    <g clip-path="url(#frontClip)">
      <polygon class="frame-outer" points="130,28 280,178 130,328 -20,178"
               fill="none" stroke="var(--frame-grey)" stroke-width="18"/>
      <polygon class="frame-inner" points="130,78 240,188 130,298 20,188"
               fill="#ffffff" stroke="var(--frame-blue)" stroke-width="10"/>
    </g>
    <text class="wordmark" x="130" y="166" text-anchor="middle" font-size="42">quilmora</text>

    <text class="holder-name" x="332" y="32" text-anchor="end">Devin Holt</text>
    <text class="holder-title" x="332" y="45" text-anchor="end">President</text>

    <g class="contact-block">
      <text class="contact-line" x="316" y="104" text-anchor="end">(800) 471-2960</text>
      <text class="contact-line" x="316" y="118" text-anchor="end">sleep@quilmora.com</text>
      <text class="contact-line" x="316" y="132" text-anchor="end">www.quilmora.com</text>
      <!-- phone -->
      <rect class="contact-icon" x="322" y="96" width="6" height="9" rx="1"/>
      <!-- envelope -->
      <rect class="contact-icon" x="321" y="111" width="9" height="7"/>
      <polyline class="contact-icon" points="321,111 325.5,115 330,111"/>
      <!-- globe -->
      <circle class="contact-icon" cx="325.5" cy="129" r="4.2"/>
      <ellipse class="contact-icon" cx="325.5" cy="129" rx="1.8" ry="4.2"/>
      <line class="contact-icon" x1="321.3" y1="129" x2="329.7" y2="129"/>
    </g>
  </svg>

  <!-- Back: brand side -->
  <svg class="business-card card-back" viewBox="0 0 350 200" aria-label="Business card back">
    <defs>
      <linearGradient id="backFill" x1="0" y1="0" x2="1" y2="1">
        <stop offset="0" stop-color="var(--slate-dark)"/>
        <stop offset="0.5" stop-color="var(--slate)"/>
        <stop offset="1" stop-color="var(--slate-dark)"/>
      </linearGradient>
      <linearGradient id="arcFill" x1="0" y1="0" x2="1" y2="0">
        <stop offset="0" stop-color="var(--brand-blue-deep)"/>
        <stop offset="1" stop-color="var(--brand-blue)"/>
      </linearGradient>
      <clipPath id="backClip"><rect width="350" height="200" rx="10"/></clipPath>
    </defs>
    <rect width="350" height="200" rx="10" fill="url(#backFill)"/>
    <g clip-path="url(#backClip)">
      <circle class="side-arc" cx="-150" cy="100" r="218" fill="url(#arcFill)"/>
      <circle class="arc-rule" cx="-150" cy="100" r="212" fill="none" stroke="var(--slate-dark)" stroke-width="1.4"/>
      <circle class="side-arc" cx="500" cy="100" r="218" fill="url(#arcFill)"/>
      <circle class="arc-rule" cx="500" cy="100" r="212" fill="none" stroke="var(--slate-dark)" stroke-width="1.4"/>
    </g>
    <text class="wordmark" x="175" y="114" text-anchor="middle" font-size="44">quilmora</text>
  </svg>

</main>
</body>
</html>
```